International business needs business cards

Our company, DRV Ventures Inc. is in the business of supplying a range construction products with particular emphasis on CEMENT. We have developed our own brand - TORVAN SUPPLIES - with which to infiltrate the market. We are launching our brand of cement (TORVAN Type IS Cement) into the Caribbean which is unlike anything this market has ever seen. A monopoly has existed here for the past 60-odd years and the market has now opened to allow the importation of other brands and consumers are anxious and ready for change/improvement. We are very excited to be launching and want to make a great first impression. We will be conducting workshops and seminars (from government level to the hardware store owners) and we want our business card to give us the strong, confident introduction that we need.

Target Market(s)

construction; builders; engineers; home owners

Industry/Entity Type

Construction

Contact Information for Business Card

Marisol Depree
CEO
cell # 1 555 4180736
Ground floor,Lindell Plaza Suite 2734
George Town,Grand Cayman
Cayman Islands,KY1-4823
EMAIL: m.depree@drvventuresinc.example
web site drvventuresinc.example

COMPANY: skype info drv.ventures.example

second card
Yvette Brannock-Depree
CFO
CELL# 1 555 607 3941
George Town,Grand Cayman
Cayman Islands,KY1-4823
EMAIL: y.brannockdepree@drvventuresinc.example
website drvventuresinc.example

Requirements
Must have
• Business cards must display BOTH logos - DRV is the company and TORVAN is the brand.

```html
<!DOCTYPE html>
<html lang="en">
<head>
<meta charset="utf-8">
<title>DRV Ventures Inc. Business Card</title>
<link rel="stylesheet" href="https://fonts.googleapis.com/css2?family=Arimo:wght@400;700&display=swap">
<style>
  :root {
    --stage: #e9e6e1;
    --card-black: #0c0c0c;
    --card-white: #ffffff;
    --brand-red: #8e1c22;
    --brand-red-dark: #6e1418;
    --ink: #111111;
    --text-grey: #7a7a7a;
    --soft-grey: #9a9a9a;
  }
  * { box-sizing: border-box; margin: 0; padding: 0; }
  html, body { width: 1200px; height: 950px; overflow: hidden; }
  body {
    background: var(--stage);
    font-family: "Arimo", Arial, sans-serif;
    position: relative;
  }
  .card {
    position: absolute;
    width: 700px;
    height: 400px;
    border-radius: 4px;
    box-shadow: 0 8px 24px rgba(0,0,0,.25);
    overflow: hidden;
  }

  /* Back side */
  .card-back {
    left: 60px; top: 50px;
    background: linear-gradient(160deg, #1d1d1d 0%, var(--card-black) 55%);
  }
  .back-mark {
    position: absolute;
    left: 50%; top: 110px;
    transform: translateX(-50%);
    display: flex; align-items: center; gap: 18px;
  }
  .back-mark .square {
    width: 110px; height: 110px;
    background: var(--brand-red);
  }
  .back-mark .name {
    color: #ffffff; font-weight: 700; font-size: 44px; letter-spacing: 1px;
  }
  .back-web {
    position: absolute; left: 0; right: 0; top: 290px;
    text-align: center;
    color: #d9d9d9; font-size: 16px; letter-spacing: 4px;
  }

  /* Front side */
  .card-front {
    left: 440px; top: 500px;
    background: var(--card-white);
  }
  .company-mark {
    position: absolute; left: 40px; top: 118px;
    display: flex; align-items: center; gap: 14px;
  }
  .company-mark .square {
    width: 72px; height: 72px; background: var(--brand-red);
  }
  .company-mark .name {
    font-weight: 700; font-size: 30px; color: var(--ink);
  }
  .brand-mark {
    position: absolute; right: 60px; top: 40px;
    display: flex; align-items: center; gap: 10px;
  }
  .brand-mark .circle {
    width: 70px; height: 70px; border-radius: 50%; background: #8a8a8a;
  }
  .brand-mark .name {
    font-weight: 700; font-size: 22px; color: #555555; letter-spacing: 1px;
  }
  .name-band {
    position: absolute; left: 420px; right: 0; top: 170px; height: 60px;
    background: linear-gradient(180deg, var(--brand-red) 0%, var(--brand-red-dark) 100%);
    color: #ffffff; padding: 8px 22px 0 22px;
  }
  .name-band .person { font-weight: 700; font-size: 21px; display: block; }
  .name-band .role { font-size: 12px; display: block; text-align: right; margin-top: 2px; }
  .address {
    position: absolute; left: 128px; top: 222px;
    color: var(--text-grey); font-size: 15px; line-height: 19px;
    font-style: normal;
  }
  .contacts {
    position: absolute; left: 128px; top: 306px;
    list-style: none; color: var(--text-grey); font-size: 15px; line-height: 21px;
  }
  .contacts li { display: flex; align-items: center; gap: 8px; }
  .contacts svg { width: 13px; height: 13px; flex: none; }
</style>
</head>
<body>

  <section class="card card-back" aria-label="Card back">
    <div class="back-mark">
      <span class="square"></span>
      <span class="name">DRV</span>
    </div>
    <p class="back-web">www.drvventuresinc.example</p>
  </section>

  <section class="card card-front" aria-label="Card front">
    <div class="brand-mark">
      <span class="circle"></span>
      <span class="name">TORVAN</span>
    </div>

    <div class="company-mark">
      <span class="square"></span>
      <span class="name">DRV Ventures Inc.</span>
    </div>

    <div class="name-band">
      <span class="person">Marisol Depree</span>
      <span class="role">CEO</span>
    </div>

    <address class="address">
      Ground floor<br>
      Lindell Plaza Suite 2734<br>
      George Town,Grand Cayman<br>
      Cayman Islands,KY1-4823
    </address>

    <ul class="contacts">
      <li>
        <svg viewBox="0 0 12 12" aria-hidden="true"><rect x="3" y="0.5" width="6" height="11" rx="1" fill="none" stroke="#8e1c22" stroke-width="1.4"/><circle cx="6" cy="9.5" r="0.8" fill="#8e1c22"/></svg>
        1 555 4180736
      </li>
      <li>
        <svg viewBox="0 0 12 12" aria-hidden="true"><rect x="0.5" y="2" width="11" height="8" fill="#8e1c22"/><path d="M0.5 2 L6 6.5 L11.5 2" fill="none" stroke="#fff" stroke-width="1"/></svg>
        m.depree@drvventuresinc.example
      </li>
      <li>
        <svg viewBox="0 0 12 12" aria-hidden="true"><circle cx="6" cy="6" r="5.5" fill="#8e1c22"/><path d="M0.5 6 H11.5 M6 0.5 C3 3.5 3 8.5 6 11.5 M6 0.5 C9 3.5 9 8.5 6 11.5" fill="none" stroke="#fff" stroke-width="0.8"/></svg>
        drvventuresinc.example
      </li>
    </ul>
  </section>

</body>
</html>
```